Meadowlark Property Review is a leading provider of residential appraisal and home inspection products in S

I need a business card/logo designed that obviously describes my business. We are a residential appraisal and home inspection company in Springfield, MO. We offer residential appraisals, home inspection, pest inspection and radon gas measurement. We have been in business for 18 years and hold state certified residential appraisal licenses and OBREX certified home inspection licenses. I have a logo that I really like and will attach, but would be open to new suggestions. I like more modern designs than traditional and would like a two sided card with our services, licenses and qualifications on the back.

```html
<!DOCTYPE html>
<html lang="en">
<head>
<meta charset="utf-8">
<title>Meadowlark Property Review – Business Card</title>
<link rel="stylesheet" href="https://fonts.googleapis.com/css2?family=Open+Sans:wght@400;600;700&display=swap">
<style>
  :root {
    --stage: #ece8e2;
    --card: #ffffff;
    --ink: #2b2b2b;
    --muted: #5a5048;
    --orange: #f39a1e;
    --brown: #a07a4c;
    --shadow: rgba(60, 45, 30, 0.22);
  }
  * { box-sizing: border-box; margin: 0; padding: 0; }
  html, body { width: 1200px; height: 858px; overflow: hidden; }
  body {
    background: var(--stage);
    font-family: "Open Sans", Arial, sans-serif;
    color: var(--ink);
    position: relative;
  }
  .card {
    position: absolute;
    width: 540px;
    height: 310px;
    background: var(--card);
    box-shadow: 0 6px 18px var(--shadow);
    overflow: hidden;
  }
  .card--front { left: 40px; top: 274px; }
  .card--back { left: 620px; top: 274px; }

  .front__curve { position: absolute; inset: 0; }

  .brand-name {
    font-family: "Open Sans", Arial, sans-serif;
    font-weight: 700;
    color: var(--brown);
    line-height: 1.1;
  }
  .card--front .brand-name {
    position: absolute; left: 24px; top: 120px;
    font-size: 20px; width: 160px;
  }

  .front__illustration {
    position: absolute; left: 150px; top: 180px;
    width: 120px; height: 112px;
    border-radius: 10px;
    background: radial-gradient(circle at 45% 45%, #d9462a 0%, #c9d2da 55%, #eef1f4 100%);
  }

  .contact {
    position: absolute; left: 318px; top: 22px;
    list-style: none;
    font-size: 14px; line-height: 21px;
    white-space: nowrap;
  }
  .contact li { display: flex; align-items: flex-start; gap: 8px; }
  .contact__icon {
    flex: 0 0 10px; width: 10px; height: 10px; margin-top: 6px;
    background: var(--orange);
  }
  .contact__cont { padding-left: 18px; }

  .services {
    position: absolute; left: 30px; top: 30px;
    list-style: none; font-size: 16px; line-height: 23px;
  }
  .credentials {
    position: absolute; left: 30px; top: 200px; width: 250px;
    list-style: none; font-size: 12.5px; line-height: 18px; color: var(--muted);
  }
  .credentials__title {
    font-weight: 600; color: var(--brown); font-size: 12px;
    letter-spacing: 0.08em; text-transform: uppercase; margin-bottom: 4px;
  }
  .card--back .brand-name {
    position: absolute; left: 300px; top: 36px;
    font-size: 24px; width: 220px; text-align: right;
  }
  .card--back .rule {
    position: absolute; left: 300px; top: 128px;
    width: 220px; height: 2px; background: var(--orange);
  }
  .extras {
    position: absolute; left: 300px; top: 150px;
    list-style: none; font-size: 15px; line-height: 22px;
  }
  .extras li { display: flex; align-items: center; gap: 10px; }
  .extras svg { flex: 0 0 10px; }
</style>
</head>
<body>
  <section class="card card--front" aria-label="Card front">
    <svg class="front__curve" width="540" height="310" viewBox="0 0 540 310" aria-hidden="true">
      <path d="M0 90 Q 300 70 330 310" fill="none" stroke="var(--orange)" stroke-width="4"/>
      <path d="M20 97 Q 290 82 320 310" fill="none" stroke="var(--brown)" stroke-width="1.5"/>
    </svg>
    <div class="brand-name">Meadowlark Property Review</div>
    <div class="front__illustration" role="img" aria-label="Illustration of a red-roofed house under a magnifying glass"></div>
    <ul class="contact">
      <li><span class="contact__icon"></span>417-555-2041</li>
      <li><span class="contact__icon"></span>417-555-3187</li>
      <li><span class="contact__icon"></span>417-555-6620</li>
      <li><span class="contact__icon"></span>info@meadowlarkreview.com</li>
      <li><span class="contact__icon"></span>Meadowlark Property Review</li>
      <li class="contact__cont">480 W Larkspur Lane, Suite C</li>
      <li class="contact__cont">Springfield, MO 65810</li>
    </ul>
  </section>

  <section class="card card--back" aria-label="Card back">
    <ul class="services">
      <li>home inspection</li>
      <li>property inspection</li>
      <li>residential appraisal</li>
      <li>pest inspection</li>
      <li>radon measurement</li>
      <li>pre-sale inspection</li>
    </ul>
    <ul class="credentials">
      <li class="credentials__title">Licenses &amp; qualifications</li>
      <li>State Certified Residential Appraiser</li>
      <li>OBREX Certified Home Inspector</li>
      <li>18 years serving Springfield, MO</li>
    </ul>
    <div class="brand-name">Meadowlark Property Review</div>
    <div class="rule"></div>
    <ul class="extras">
      <li><svg width="10" height="10" viewBox="0 0 10 10"><path d="M1 9 L9 1 M1 9 L7 9" stroke="var(--orange)" stroke-width="2.2" fill="none"/></svg>thermal imaging</li>
      <li><svg width="10" height="10" viewBox="0 0 10 10"><path d="M1 9 L9 1 M1 9 L7 9" stroke="var(--orange)" stroke-width="2.2" fill="none"/></svg>mechanical inspection</li>
      <li><svg width="10" height="10" viewBox="0 0 10 10"><path d="M1 9 L9 1 M1 9 L7 9" stroke="var(--orange)" stroke-width="2.2" fill="none"/></svg>tax appeal</li>
      <li><svg width="10" height="10" viewBox="0 0 10 10"><path d="M1 9 L9 1 M1 9 L7 9" stroke="var(--orange)" stroke-width="2.2" fill="none"/></svg>asset evaluation</li>
      <li><svg width="10" height="10" viewBox="0 0 10 10"><path d="M1 9 L9 1 M1 9 L7 9" stroke="var(--orange)" stroke-width="2.2" fill="none"/></svg>energy audits</li>
    </ul>
  </section>
</body>
</html>
```